design a construction company business card

Design business card around our logo. Card must have all the typical info: name, title, address, phone, email, business name, etc. Somewhere on the card I would like to see our motto "Grounded in trust... Driven by dedication." Consider adding a splash of bright orange to the card to complement the blues and silvers/grays in the logo. We are open to metallic inks, textures, etc. We would like to see options on both light and dark backgrounds. The font in the logo is Euro Technic Extended Regular.

```html
<!DOCTYPE html>
<html lang="en">
<head>
<meta charset="utf-8">
<title>Harlow Contracting, Inc. — Business Card</title>
<link rel="stylesheet" href="https://fonts.googleapis.com/css2?family=Michroma&family=Roboto:wght@400&display=swap">
<style>
  :root {
    --backdrop-light: #6a6a6c;
    --backdrop-dark: #2c2c2e;
    --card-top: #2b2b2d;
    --card-bottom: #141415;
    --brand-blue: #1f6fd6;
    --text-silver: #c9cbcf;
    --icon-blue: #2a7be0;
    --icon-cut: #141415;
  }
  * { margin: 0; padding: 0; box-sizing: border-box; }
  html, body { width: 1200px; height: 1000px; overflow: hidden; }
  body {
    position: relative;
    background: radial-gradient(ellipse at 50% 35%, var(--backdrop-light), var(--backdrop-dark) 80%);
    font-family: "Roboto", Arial, sans-serif;
  }
  .card {
    position: absolute;
    width: 640px;
    height: 366px;
    border-radius: 22px;
    background: linear-gradient(160deg, var(--card-top), var(--card-bottom));
    box-shadow: 0 18px 40px rgba(0,0,0,0.55);
    overflow: hidden;
  }
  .card-front { left: 470px; top: 70px; }
  .card-back { left: 90px; top: 490px; }

  .wordmark {
    font-family: "Michroma", "Arial Black", sans-serif;
    color: var(--brand-blue);
    font-weight: 400;
    text-transform: uppercase;
  }
  .wordmark .name { display: block; font-size: 52px; letter-spacing: 4px; line-height: 1; }
  .wordmark .suffix { display: block; font-size: 15px; letter-spacing: 2px; margin-top: 10px; }

  .card-front .wordmark {
    position: absolute; left: 0; right: 0; top: 110px; text-align: center;
  }
  .motto {
    position: absolute; left: 0; right: 0; top: 262px; text-align: center;
    font-family: "Michroma", "Arial Black", sans-serif;
    font-size: 11.5px; letter-spacing: 1.2px;
    color: var(--brand-blue); text-transform: uppercase;
  }

  .card-back .wordmark { position: absolute; left: 60px; top: 70px; }
  .card-back .wordmark .name { font-size: 46px; }
  .card-back .wordmark .suffix { font-size: 13px; }

  .contact {
    position: absolute; left: 370px; top: 198px;
    color: var(--text-silver); font-size: 15px; line-height: 1.3;
  }
  .contact .person {
    font-family: "Michroma", "Arial Black", sans-serif;
    color: var(--brand-blue); font-size: 17px; letter-spacing: 0.5px;
  }
  .contact .title { margin-bottom: 10px; }
  .contact .address { margin-bottom: 6px; }
  .contact .line { display: flex; align-items: center; gap: 8px; }
  .contact .line svg { width: 12px; height: 12px; flex: none; }
  .contact .web-accent { color: var(--brand-blue); }
</style>
</head>
<body>
  <section class="card card-front">
    <div class="wordmark">
      <span class="name">Harlow</span>
      <span class="suffix">Contracting, Inc.</span>
    </div>
    <p class="motto">Grounded in trust... Driven by dedication.</p>
  </section>

  <section class="card card-back">
    <div class="wordmark">
      <span class="name">Harlow</span>
      <span class="suffix">Contracting, Inc.</span>
    </div>
    <div class="contact">
      <p class="person">Marcus Reed</p>
      <p class="title">Managing Director</p>
      <p class="address">4870 Ridge Avenue N.Y.<br>Lakeside AB T1R</p>
      <p class="line">
        <svg viewBox="0 0 12 12" aria-hidden="true"><circle cx="6" cy="6" r="6" fill="var(--icon-blue)"/><path d="M4 3.2l1 1.3-.6.7c.4.9 1 1.5 1.9 1.9l.7-.6 1.3 1-.6 1.1C5.6 8.4 3.6 6.4 3.4 4.3z" fill="var(--icon-cut)"/></svg>
        <span>555.014.2700</span>
      </p>
      <p class="line">
        <svg viewBox="0 0 12 12" aria-hidden="true"><rect x="0.5" y="2" width="11" height="8" rx="1" fill="var(--icon-blue)"/><path d="M1 3l5 3.5L11 3" stroke="var(--icon-cut)" stroke-width="1" fill="none"/></svg>
        <span>marcus@harlowbuild.com</span>
      </p>
      <p class="line">
        <svg viewBox="0 0 12 12" aria-hidden="true"><circle cx="6" cy="6" r="5.5" fill="var(--icon-blue)"/><path d="M0.5 6h11M6 0.5c-2 2.5-2 8.5 0 11M6 0.5c2 2.5 2 8.5 0 11" stroke="var(--icon-cut)" stroke-width="0.8" fill="none"/></svg>
        <span>www.<span class="web-accent">harlowbuild</span>.com</span>
      </p>
    </div>
  </section>
</body>
</html>
```